Talvique Hotels Business Card and Logo

We need a business card design for a hotel group. I saw a hotel card you designed and really liked it. We have multiple properties with different brands. Were hoping that the card would be unique and find a way to list out all our properties. Our web address is www.talviquehotels.com. I have attached some photos of card designs I like.

Industry/Entity Type

Hotel

Contact Information for Business Card

Scott CurranReneson HotelsChief Operating Officer56 Madera DriveCorte Madera, CA 94925Office 415-891-5013Cell 707-5550143

```html
<!DOCTYPE html>
<html lang="en">
<head>
<meta charset="utf-8">
<title>Talvique Hotels Business Card</title>
<link href="https://fonts.googleapis.com/css2?family=Oswald:wght@300;400;500;600&display=swap" rel="stylesheet">
<style>
  :root {
    --backdrop: #8f8f8f;
    --card-blue: #7b96a6;
    --card-blue-light: #93aebd;
    --card-white: #ffffff;
    --card-white-shade: #eef0f2;
    --ink-blue: #3f6178;
    --ink-dark: #2b2b2b;
    --ink-light: #ffffff;
  }
  * { margin: 0; padding: 0; box-sizing: border-box; }
  html, body { width: 1200px; height: 941px; overflow: hidden; }
  body {
    background: var(--backdrop);
    font-family: "Oswald", sans-serif;
    position: relative;
  }
  .card {
    position: absolute;
    width: 600px;
    height: 343px;
    border-radius: 18px;
    overflow: hidden;
  }
  .card-back {
    left: 330px;
    top: 60px;
    background: radial-gradient(circle at 55% 55%, var(--card-blue-light), var(--card-blue) 70%);
    color: var(--ink-light);
    text-align: center;
  }
  .card-front {
    left: 260px;
    top: 480px;
    background: linear-gradient(160deg, var(--card-white) 40%, var(--card-white-shade));
    text-align: center;
  }
  .brand-mark {
    display: inline-block;
    width: 18px;
    height: 18px;
    border-radius: 50%;
    background: currentColor;
    margin-right: 12px;
    vertical-align: middle;
  }
  .card-back .brand-name {
    margin-top: 110px;
    font-size: 54px;
    font-weight: 600;
    line-height: 1;
  }
  .card-back .tagline {
    margin-top: 8px;
    font-size: 9.5px;
    font-weight: 500;
    letter-spacing: 0.3px;
  }
  .web-address {
    margin-top: 34px;
    font-size: 26px;
    font-weight: 300;
    letter-spacing: 3px;
  }
  .card-front .brand-name {
    margin-top: 34px;
    font-size: 32px;
    font-weight: 600;
    color: var(--ink-blue);
    line-height: 1;
  }
  .card-front .tagline {
    margin-top: 4px;
    font-size: 6.5px;
    font-weight: 500;
    color: var(--ink-blue);
  }
  .person-name {
    margin-top: 16px;
    font-size: 36px;
    font-weight: 600;
    color: var(--ink-blue);
    line-height: 1;
  }
  .person-title {
    margin-top: 4px;
    font-size: 22px;
    font-weight: 400;
    color: var(--ink-dark);
  }
  .divider {
    margin: 10px 0 10px;
    height: 2px;
    background: var(--ink-blue);
  }
  .contact-line {
    font-size: 22px;
    font-weight: 400;
    color: var(--ink-dark);
    line-height: 1.25;
  }
</style>
</head>
<body>
  <section class="card card-back" aria-label="Card back">
    <div class="brand-name"><span class="brand-mark"></span>Talvique Hotels</div>
    <div class="tagline">RESTFUL STAYS IN THE FINEST COASTAL, VALLEY &amp; HILLSIDE DESTINATIONS OF THE WEST</div>
    <div class="web-address">www.talviquehotels.com</div>
  </section>

  <section class="card card-front" aria-label="Card front">
    <div class="brand-name"><span class="brand-mark"></span>Talvique Hotels</div>
    <div class="tagline">RESTFUL STAYS IN THE FINEST COASTAL, VALLEY &amp; HILLSIDE DESTINATIONS OF THE WEST</div>
    <div class="person-name">Brent Holloway Talvique</div>
    <div class="person-title">Hotels Chief Operating Officer</div>
    <div class="divider"></div>
    <div class="contact-line">83 Pellwick Lane, Larkmoor, CA 94917</div>
    <div class="contact-line">Office : 415-555-0186</div>
    <div class="contact-line">Cell : 707-5550143</div>
  </section>
</body>
</html>
```